Wine Label design for a Grapefruit flavored wine

We need a wine label for a wine that is flavored with grapefruit flavors and slightly sparkling.It should be eye catching and fun. It will be sold in the United States market. We like the idea of using a pink flamingo and/or grapefruits. Just one flamingo please if you use a flamingo. There is no size restriction on the label size. Something super eye catching and super fun.

Attached are some images we like, these are for your reference only, they are not good quality for print. You can choose to do something with a flamingo or with grapefruits or both together. Something bold is what we are looking for too. You can even use a clear label. We really don't mind seeing some fun and bold colors.

The name of the wine is: Vela di Corallo
In small letters please put this sentence:

Grape wine with natural grapefruit, peach flavor, carbonation added
It is a white wine in a clear Bordeaux style bottle with a screw cap.

```html
<!DOCTYPE html>
<html lang="en">
<head>
<meta charset="utf-8">
<title>Vela di Corallo – Wine Label</title>
<link rel="stylesheet" href="https://fonts.googleapis.com/css2?family=Cinzel:wght@700&family=Libre+Baskerville:wght@700&display=swap">
<style>
  :root {
    --backdrop: #efedf0;
    --paper: #f4eee8;
    --paper-edge: #e9e1da;
    --magenta: #e0459a;
    --magenta-deep: #c8287f;
    --ray-pink: #f2c3d9;
    --ink-pink: #d93a8c;
    --cream-text: #fdf5f2;
    --fruit: #ee6f8d;
  }
  * { box-sizing: border-box; margin: 0; padding: 0; }
  html, body { width: 1200px; height: 800px; overflow: hidden; }
  body { background: var(--backdrop); position: relative; }

  .wine-label {
    position: absolute;
    left: 440px; top: 30px;
    width: 320px; height: 740px;
    background: linear-gradient(180deg, var(--paper) 0%, var(--paper-edge) 100%);
  }
  .sunburst {
    position: absolute;
    left: 0; top: 40px; width: 320px; height: 480px;
    background: radial-gradient(ellipse at 50% 50%, var(--ray-pink) 0%, rgba(242,195,217,0.45) 45%, rgba(242,195,217,0) 72%);
  }
  .side-rule {
    position: absolute; top: 408px; bottom: 10px; width: 1px;
    background: var(--ink-pink); opacity: .7;
  }
  .side-rule.left { left: 14px; }
  .side-rule.right { right: 14px; }

  .flamingo {
    position: absolute; left: 141px; top: 20px;
    width: 38px; height: 70px;
    background: var(--magenta); border-radius: 19px 19px 6px 6px;
  }
  .dash-rule {
    position: absolute; top: 66px; height: 0;
    border-top: 1px dashed var(--ink-pink);
  }
  .dash-rule.left { left: 10px; width: 122px; }
  .dash-rule.right { left: 204px; width: 100px; }

  .name-plaque {
    position: absolute; left: -15px; top: 133px;
    width: 350px; height: 275px;
  }
  .name-plaque svg { position: absolute; inset: 0; }
  .plaque-ornament {
    position: absolute; left: 130px; width: 90px; height: 20px;
    background: rgba(253,245,242,0.75); border-radius: 10px;
  }
  .plaque-ornament.top { top: 40px; }
  .plaque-ornament.bottom { top: 220px; height: 14px; width: 160px; left: 95px; }
  .wine-name {
    position: absolute; left: 0; right: 0; top: 72px;
    text-align: center; color: var(--cream-text);
    font-family: "Cinzel", "Libre Baskerville", serif; font-weight: 700;
    line-height: 1;
  }
  .wine-name .line-one { display: block; font-size: 72px; letter-spacing: -1px; }
  .wine-name .line-two { display: block; font-size: 44px; margin-top: 8px; letter-spacing: 0; }

  .fruit-row {
    position: absolute; left: 65px; top: 503px;
    width: 192px; height: 70px;
    background: var(--fruit); border-radius: 35px;
  }
  .wine-description {
    position: absolute; left: 20px; right: 20px; top: 600px;
    text-align: center; color: var(--ink-pink);
    font-family: "Libre Baskerville", serif; font-weight: 700;
    font-size: 9.6px; line-height: 14.5px; text-transform: uppercase;
  }
  .footer-rule {
    position: absolute; left: 85px; width: 150px; top: 677px;
    border-top: 1px solid var(--ink-pink);
  }
  .footer-ornament {
    position: absolute; left: 110px; top: 681px;
    width: 100px; height: 16px;
    background: var(--magenta); opacity: .8; border-radius: 8px;
  }
</style>
</head>
<body>
  <main class="wine-label">
    <div class="sunburst" role="img" aria-label="Soft pink sunburst rays radiating behind the name plaque"></div>
    <div class="side-rule left"></div>
    <div class="side-rule right"></div>

    <div class="dash-rule left"></div>
    <div class="dash-rule right"></div>
    <div class="flamingo" role="img" aria-label="Pink flamingo silhouette standing on one leg"></div>

    <div class="name-plaque">
      <svg viewBox="0 0 350 275" width="350" height="275" aria-hidden="true">
        <defs>
          <linearGradient id="plaque-fill" x1="0" y1="0" x2="0" y2="1">
            <stop offset="0" stop-color="#e654a4"/>
            <stop offset="1" stop-color="#cf2f86"/>
          </linearGradient>
        </defs>
        <path d="M30,0 H320 Q320,30 350,30 V245 Q320,245 320,275 H30 Q30,245 0,245 V30 Q30,30 30,0 Z" fill="url(#plaque-fill)"/>
        <path d="M38,8 H312 Q314,36 342,38 V237 Q314,239 312,267 H38 Q36,239 8,237 V38 Q36,36 38,8 Z" fill="none" stroke="#fbe3ef" stroke-width="1.5"/>
      </svg>
      <div class="plaque-ornament top" role="img" aria-label="Cream scroll flourish"></div>
      <h1 class="wine-name">
        <span class="line-one">VELA DI</span>
        <span class="line-two">CORALLO</span>
      </h1>
      <div class="plaque-ornament bottom" role="img" aria-label="Cream scroll flourish"></div>
    </div>

    <div class="fruit-row" role="img" aria-label="Three pink grapefruit slices in a row"></div>

    <p class="wine-description">
      Grape wine with natural grapefruit,<br>
      peach flavor, carbonation added<br>
      It is a white wine in a clear Bordeaux<br>
      style bottle with a screw cap.
    </p>

    <div class="footer-rule"></div>
    <div class="footer-ornament" role="img" aria-label="Pink scroll flourish"></div>
  </main>
</body>
</html>
```